Business Card Design

Online clothing womens clothing store, I sell my clothing online and at the markets.

i would like the attached picture on the front of the card and the contact information on the back.

Industry/Entity Type

Business

Contact Information for Business Card

Marlow Thread
Karen Whitfield
(Instagram symbol) _marlow_thread_
(Facebook symbol) www.fakebookexample.com/marlowthreadau/

W : www.marlowthread.example.au
E : info@marlowthread.example.au
P : 0498716204

```html
<!DOCTYPE html>
<html lang="en">
<head>
<meta charset="utf-8">
<title>Marlow Thread – Business Card</title>
<link href="https://fonts.googleapis.com/css2?family=Lato:wght@300;400;700;900&display=swap" rel="stylesheet">
<style>
  :root{
    --stage:#2b2b2b;
    --ink:#111111;
    --paper:#ffffff;
    --paper-shade:#e6e6e6;
    --muted:#3a3a3a;
    --photo-light:#dfe4e4;
    --photo-mid:#8fa6a8;
    --photo-dark:#3e3c48;
  }
  *{box-sizing:border-box;margin:0;padding:0}
  html,body{width:1200px;height:997px;overflow:hidden}
  body{background:var(--stage);font-family:'Lato',sans-serif;position:relative}

  .card{position:absolute;left:240px;width:720px;height:412px;overflow:hidden;box-shadow:0 10px 30px rgba(0,0,0,.5)}
  .card--front{top:48px}
  .card--back{top:520px;background:linear-gradient(180deg,var(--paper) 0%,var(--paper-shade) 100%);color:var(--ink)}

  .front-photo{position:absolute;inset:0;background:
      radial-gradient(ellipse at 70% 30%,var(--photo-dark) 0%,rgba(62,60,72,.6) 30%,transparent 60%),
      linear-gradient(120deg,var(--photo-mid) 0%,var(--photo-light) 45%,#c9cccd 100%)}
  .front-name{position:absolute;left:40px;bottom:40px;font-weight:700;font-size:58px;letter-spacing:4px;color:rgba(255,255,255,.9);text-transform:uppercase}

  .brand{position:absolute;top:22px;left:250px;font-weight:400;font-size:28px;letter-spacing:8px;text-transform:uppercase}
  .band{position:absolute;left:0;width:100%;background:var(--ink);color:var(--paper)}
  .band--top{top:66px;height:20px}
  .band--name{top:160px;height:34px;display:flex;align-items:center;padding-left:40px;gap:14px}
  .band--offer{top:324px;height:34px;display:flex;align-items:center;padding-left:40px;font-size:17px}
  .person{font-weight:900;font-size:21px;text-transform:uppercase}
  .divider{width:1px;height:20px;background:var(--paper)}
  .role{font-weight:400;font-size:14px}

  .contact{position:absolute;display:flex;flex-direction:column;gap:8px;font-size:15px}
  .contact li{list-style:none;display:flex;align-items:center;gap:10px}
  .contact--social{top:106px;left:450px;font-size:13px}
  .contact--direct{top:246px;left:40px;font-size:16px}
  .icon{width:16px;height:16px;flex:none}
  .social-mark{width:14px;height:14px;background:var(--ink);border-radius:3px;flex:none}
  .delivery{position:absolute;top:212px;right:40px;font-size:16px;color:var(--muted)}
  .web{position:absolute;bottom:16px;left:0;width:100%;text-align:center;font-size:17px;letter-spacing:6px;color:var(--muted)}
</style>
</head>
<body>

<section class="card card--front">
  <div class="front-photo" role="img" aria-label="Misty coastal landscape photograph supplied by the client"></div>
  <p class="front-name">Marlow Thread</p>
</section>

<section class="card card--back">
  <p class="brand">Marlow Thread</p>
  <div class="band band--top"></div>

  <ul class="contact contact--social">
    <li><span class="social-mark"></span>_marlow_thread_</li>
    <li><span class="social-mark"></span>info@marlowthread.example.au</li>
  </ul>

  <div class="band band--name">
    <span class="person">Karen Whitfield</span>
    <span class="divider"></span>
    <span class="role">Owner</span>
  </div>

  <p class="delivery">&raquo; Worldwide Delivery &laquo;</p>

  <ul class="contact contact--direct">
    <li>
      <svg class="icon" viewBox="0 0 16 16"><rect x="3.5" y="1" width="9" height="14" rx="1.5" fill="none" stroke="#111" stroke-width="1.5"/><line x1="6.5" y1="12.5" x2="9.5" y2="12.5" stroke="#111" stroke-width="1.2"/></svg>
      0498716204
    </li>
    <li>
      <svg class="icon" viewBox="0 0 16 16"><rect x="1" y="3" width="14" height="10" fill="none" stroke="#111" stroke-width="1.5"/><polyline points="1,3 8,9 15,3" fill="none" stroke="#111" stroke-width="1.5"/></svg>
      info@marlowthread.example.au
    </li>
  </ul>

  <div class="band band--offer">&raquo; Free shipping over $75.00 &laquo;</div>

  <p class="web">www.marlowthread.example.au</p>
</section>

</body>
</html>
```